Corporate Travel Technology Company needs new Business Card design

We need a new business card design to reflect our re-branded company. Our company is called tolvEn (pronounced tolvenn) and we provide Business Intelligence and mobile travel management solutions for the corporate travel industry. Our multinational customers use our solutions to manage large travel budgets and frequent travellers, as well as to save money and reduce risk. We'd like to see designs that use the blue and green palette as well as our corporate logo (attached below). The design should communicate innovation, insight, forward thinking, contemporary, trusted.

Target Market(s)

Large multinational corporates and Travel Agencies.

Industry/Entity Type

Business

Contact Information for Business Card

Rosalind Mercer
Chief Executive
tolvEn
Phone number - +61 (0)2 8134 2907
Email address - rosalind.mercer@tolven-example.com
Mobile number - +61 (0)438 516 702
www.tolven-example.com

Font styles to use
Other font styles liked:
• Please use font as close to corporate logo as possible

Colors
0255a3
0393ce
00a990
33b8a4
33a6d7
3176b5

Requirements
Must have
• Please include the words;
• Mobile Travel Management
• Accelerating Travel Business Insights
• Use corporate logo - although icon can be stylised if needed

```html
<!DOCTYPE html>
<html lang="en">
<head>
<meta charset="utf-8">
<title>tolvEn business card</title>
<link href="https://fonts.googleapis.com/css2?family=Arimo:wght@400;700&display=swap" rel="stylesheet">
<style>
  :root {
    --blue-deep: #0255a3;
    --blue-bright: #0393ce;
    --blue-mid: #3176b5;
    --blue-soft: #33a6d7;
    --teal: #00a990;
    --teal-light: #33b8a4;
    --ink: #1d1d1d;
    --card-white: #ffffff;
    --card-black: #0b0b0b;
    --backdrop: #e6e8ea;
  }
  * { margin: 0; padding: 0; box-sizing: border-box; }
  html, body { width: 1200px; height: 892px; overflow: hidden; }
  body {
    background: var(--backdrop);
    font-family: "Arimo", Arial, sans-serif;
    position: relative;
  }
  .card {
    position: absolute;
    left: 320px;
    width: 560px;
    height: 320px;
    border-radius: 4px;
    overflow: hidden;
    box-shadow: 0 6px 18px rgba(0,0,0,0.18);
  }
  .card-front { top: 76px; background: var(--card-white); }
  .card-back { top: 496px; background: var(--card-black); }

  .front-shape { position: absolute; inset: 0; }

  .wordmark {
    display: flex;
    align-items: center;
    gap: 10px;
    font-weight: 400;
    color: var(--blue-bright);
    line-height: 1;
  }
  .wordmark-dot {
    border-radius: 50%;
    background: var(--blue-bright);
    flex: none;
  }
  .card-front .wordmark {
    position: absolute;
    left: 114px; top: 136px;
    font-size: 40px;
  }
  .card-front .wordmark-dot { width: 20px; height: 20px; }

  .divider {
    position: absolute;
    left: 286px; top: 60px;
    width: 1.5px; height: 200px;
    background: var(--teal-light);
  }

  .identity { position: absolute; left: 302px; top: 62px; }
  .person-name {
    font-size: 24px; font-weight: 700;
    color: var(--blue-bright);
    letter-spacing: 0.2px;
  }
  .person-role {
    font-size: 13.5px; color: var(--ink);
    margin-top: 4px;
  }

  .contact-list {
    position: absolute; left: 302px; top: 170px;
    list-style: none;
  }
  .contact-item {
    display: flex; align-items: center; gap: 7px;
    font-size: 11.5px; color: var(--ink);
    height: 19px;
    white-space: nowrap;
  }
  .contact-icon { width: 11px; height: 11px; flex: none; }

  .back-brand {
    position: absolute;
    left: 50%; top: 50%;
    transform: translate(-50%, -50%);
    display: flex;
    flex-direction: column;
    align-items: center;
  }
  .card-back .wordmark {
    font-size: 60px;
    color: var(--teal-light);
  }
  .card-back .wordmark-dot { width: 28px; height: 28px; background: var(--blue-bright); }
  .tagline {
    font-size: 13px;
    letter-spacing: 1.2px;
    text-transform: uppercase;
    margin-top: 18px;
    color: var(--blue-soft);
  }
  .tagline + .tagline {
    margin-top: 7px;
    color: var(--teal-light);
  }
</style>
</head>
<body>

<section class="card card-front" aria-label="Card front">
  <svg class="front-shape" width="560" height="320" viewBox="0 0 560 320" aria-hidden="true">
    <defs>
      <linearGradient id="frontBlue" x1="0" y1="0" x2="1" y2="1">
        <stop offset="0" stop-color="#3176b5"/>
        <stop offset="1" stop-color="#0393ce"/>
      </linearGradient>
    </defs>
    <rect width="560" height="320" fill="url(#frontBlue)"/>
    <circle cx="500" cy="150" r="405" fill="#ffffff"/>
  </svg>

  <div class="wordmark"><span class="wordmark-dot"></span><span>tolvEn</span></div>

  <div class="divider"></div>

  <div class="identity">
    <p class="person-name">Rosalind Mercer</p>
    <p class="person-role">Chief Executive</p>
  </div>

  <ul class="contact-list">
    <li class="contact-item">
      <svg class="contact-icon" viewBox="0 0 11 11" aria-hidden="true"><rect width="11" height="11" rx="2" fill="#0393ce"/><path d="M3 2.5l1.5 0 .6 1.6-.9.7a5 5 0 0 0 2 2l.7-.9 1.6.6v1.5a1 1 0 0 1-1 .6A6 6 0 0 1 2.4 3.5a1 1 0 0 1 .6-1z" fill="#fff"/></svg>
      +61 (0)2 8134 2907
    </li>
    <li class="contact-item">
      <svg class="contact-icon" viewBox="0 0 11 11" aria-hidden="true"><rect width="11" height="11" rx="2" fill="#0393ce"/><rect x="3.5" y="2" width="4" height="7" rx="0.8" fill="#fff"/></svg>
      +61 (0)438 516 702
    </li>
    <li class="contact-item">
      <svg class="contact-icon" viewBox="0 0 11 11" aria-hidden="true"><rect width="11" height="11" rx="2" fill="#0393ce"/><circle cx="5.5" cy="5.5" r="3" fill="none" stroke="#fff" stroke-width="1"/><path d="M2.5 5.5h6M5.5 2.5v6" stroke="#fff" stroke-width="0.8"/></svg>
      www.tolven-example.com
    </li>
    <li class="contact-item">
      <svg class="contact-icon" viewBox="0 0 11 11" aria-hidden="true"><rect width="11" height="11" rx="2" fill="#0393ce"/><rect x="2.2" y="3.2" width="6.6" height="4.6" fill="#fff"/><path d="M2.2 3.2l3.3 2.6 3.3-2.6" fill="none" stroke="#0393ce" stroke-width="0.8"/></svg>
      rosalind.mercer@tolven-example.com
    </li>
  </ul>
</section>

<section class="card card-back" aria-label="Card back">
  <div class="back-brand">
    <div class="wordmark"><span class="wordmark-dot"></span><span>tolvEn</span></div>
    <p class="tagline">Mobile Travel Management</p>
    <p class="tagline">Accelerating Travel Business Insights</p>
  </div>
</section>

</body>
</html>
```